Kelvaro.ch is looking for business card letterhead and envelope C5 with WOW effect

We need a strong business card for our company Kelvaro.ch, logo is available. You want a black or dark background on which the logo Stark r% 26 # 252; appears. Letterhead and envelope in C5 format should be in a similar design, but does not have to be We need a strong business card for our company Kelvaro.ch, logo is available. A black or dark background is desired, on which the logo Stark comes across. The letterhead and the envelope in C5 format should have a similar design.

Target Market(s)

Private customers as well as entrepreneurs

Contact Information for Business Card

E-mail: info@kelvaro-example.ch
Web.www.Kelvaro-example.ch
Tel: +41 ( 0 ) 79 482 6037
Adresse:
Lindenweg 14
9406 Tarnbach

Hier kann man Icons verwenden für Email,Tel und Adressse

Font styles to use
Other font styles liked:
• Dubai,bold

Colors

Designer to choose colors to be used in the design.

Requirements
Must have
• WOW effect
Nice to have
• R% 26 # 252; back business card with our service listings. - VEHICLE LABELING - SHOP WINDOW LABELING - STICKERS AND MUCH MORE ... in red color

```html
<!DOCTYPE html>
<html lang="en">
<head>
<meta charset="utf-8">
<title>Kelvaro.ch Business Card</title>
<link href="https://fonts.googleapis.com/css2?family=Oswald:wght@500&family=Roboto:wght@300;400;500&display=swap" rel="stylesheet">
<style>
  :root {
    --page-bg: #2a2a2a;
    --card-bg: #1e1e1e;
    --accent: #f5c518;
    --text-light: #e6e6e6;
    --text-muted: #bdbdbd;
    --logo-grey: #4a4a4a;
    --divider: #6a6a6a;
  }
  * { box-sizing: border-box; margin: 0; padding: 0; }
  html, body { width: 1200px; height: 880px; overflow: hidden; }
  body {
    background: var(--page-bg);
    font-family: "Roboto", Arial, sans-serif;
    position: relative;
  }
  .card {
    position: absolute;
    left: 250px;
    width: 700px;
    height: 400px;
    background: var(--card-bg);
    border-radius: 22px;
    overflow: hidden;
    box-shadow: 0 10px 30px rgba(0,0,0,0.45);
  }
  .card::after {
    content: "";
    position: absolute;
    left: 0; right: 0; bottom: 0;
    height: 9px;
    background: var(--accent);
  }
  .card--services { top: 25px; }
  .card--contact { top: 455px; }

  /* Services side */
  .brand-name {
    position: absolute;
    left: 0; right: 0;
    top: 95px;
    text-align: center;
    font-family: "Roboto", Arial, sans-serif;
    font-weight: 500;
    font-size: 54px;
    letter-spacing: 2px;
    color: var(--logo-grey);
    text-transform: uppercase;
  }
  .services-title {
    position: absolute;
    left: 0; right: 0;
    top: 205px;
    text-align: center;
    color: var(--accent);
    font-size: 30px;
    font-weight: 500;
  }
  .services-list {
    position: absolute;
    left: 0; right: 0;
    top: 258px;
    text-align: center;
    color: var(--text-light);
    font-weight: 300;
    font-size: 19px;
    line-height: 30px;
    letter-spacing: 0.3px;
  }
  .services-list .dot {
    display: inline-block;
    width: 9px; height: 9px;
    border-radius: 50%;
    background: var(--accent);
    margin: 0 6px 2px;
  }

  /* Contact side */
  .person {
    position: absolute;
    left: 70px;
    top: 130px;
    text-align: right;
    width: 300px;
  }
  .person__name {
    font-family: "Oswald", "Arial Narrow", sans-serif;
    font-weight: 500;
    font-size: 44px;
    color: var(--accent);
    line-height: 1.05;
    letter-spacing: 0.5px;
  }
  .person__role {
    font-size: 20px;
    font-weight: 300;
    color: var(--text-light);
  }
  .divider {
    position: absolute;
    left: 395px;
    top: 115px;
    width: 1px;
    height: 105px;
    background: var(--divider);
  }
  .contact-list {
    position: absolute;
    left: 420px;
    top: 118px;
    list-style: none;
    color: var(--text-light);
    font-weight: 300;
    font-size: 19px;
    line-height: 33px;
  }
  .contact-list li { display: flex; align-items: center; gap: 10px; }
  .contact-list svg { width: 16px; height: 16px; flex: none; fill: var(--accent); }
  .contact-list .highlight { color: var(--accent); }
  .address {
    position: absolute;
    left: 0; right: 0;
    top: 318px;
    display: flex;
    justify-content: center;
    align-items: center;
    gap: 10px;
    color: var(--text-light);
    font-weight: 300;
    font-size: 20px;
  }
  .address svg { width: 16px; height: 20px; fill: var(--accent); }
</style>
</head>
<body>
  <section class="card card--services">
    <div class="brand-name">Kelvaro.ch</div>
    <div class="services-title">our service listings</div>
    <div class="services-list">
      VEHICLE LABELING<span class="dot"></span>SHOP WINDOW LABELING<br>
      STICKERS AND MUCH MORE
    </div>
  </section>

  <section class="card card--contact">
    <div class="person">
      <div class="person__name">MARLEN VOGT</div>
      <div class="person__role">Manager</div>
    </div>
    <div class="divider"></div>
    <ul class="contact-list">
      <li>
        <svg viewBox="0 0 24 24" aria-hidden="true"><path d="M6.6 10.8a15.1 15.1 0 0 0 6.6 6.6l2.2-2.2a1 1 0 0 1 1-.25 11.4 11.4 0 0 0 3.6.57 1 1 0 0 1 1 1V20a1 1 0 0 1-1 1A17 17 0 0 1 3 4a1 1 0 0 1 1-1h3.5a1 1 0 0 1 1 1c0 1.25.2 2.45.57 3.57a1 1 0 0 1-.25 1z"/></svg>
        +41 ( 0 ) 79 482 6037
      </li>
      <li>
        <svg viewBox="0 0 24 24" aria-hidden="true"><path d="M2 5h20v14H2z M2 5l10 8 10-8" fill="none" stroke="#f5c518" stroke-width="2"/></svg>
        info@kelvaro-example.ch
      </li>
      <li>
        <svg viewBox="0 0 24 24" aria-hidden="true"><circle cx="12" cy="12" r="10" fill="none" stroke="#f5c518" stroke-width="2"/><path d="M2 12h20M12 2c3 3 3 17 0 20M12 2c-3 3-3 17 0 20" fill="none" stroke="#f5c518" stroke-width="1.6"/></svg>
        <span>www.<span class="highlight">Kelvaro-example</span>.ch</span>
      </li>
    </ul>
    <div class="address">
      <svg viewBox="0 0 16 20" aria-hidden="true"><path d="M8 0a7 7 0 0 0-7 7c0 5 7 13 7 13s7-8 7-13a7 7 0 0 0-7-7zm0 10a3 3 0 1 1 0-6 3 3 0 0 1 0 6z"/></svg>
      Lindenweg 14, 9406 Tarnbach
    </div>
  </section>
</body>
</html>
```